Website for Torvel Capital - investment banking firm

We have a corporate identity (thanks to Ravinka/31842) and want to extend that into a website design.  See the attached zipped files.
We have software folks in-house to do the coding.
See the attached Project Brief & Notes for more details.  Don't worry about the actual text - lorem ipsum will be fine.
The server will be Apache.
Thank you!
Desmond

Industry/Entity Type
Investment

```html
<!DOCTYPE html>
<html lang="en">
<head>
<meta charset="utf-8">
<title>Torvel Capital</title>
<link rel="stylesheet" href="https://fonts.googleapis.com/css2?family=Raleway:wght@400;500&family=Open+Sans:wght@400;600&display=swap">
<style>
:root{
  --navy:#1f3d7a;
  --blue:#3a78cf;
  --link:#2a6fc9;
  --text:#333;
  --muted:#777;
  --rule:#e3e3e3;
  --panel:#f0f0f0;
  --dark:#1f1f1f;
  --darker:#111;
  --footer-text:#e6e6e6;
}
*{box-sizing:border-box;margin:0;padding:0}
html,body{width:1125px;height:1200px;overflow:hidden;background:#fff}
body{font-family:"Open Sans",Arial,sans-serif;color:var(--text);position:relative}
.page{position:absolute;left:103px;top:0;width:919px;height:1200px}
.top-rule{position:absolute;left:0;top:0;width:919px;height:3px;background:#4a4a4a}

.brand{position:absolute;left:2px;top:32px;display:flex;align-items:center;gap:10px}
.brand-mark{width:40px;height:40px;border-radius:50%;background:var(--navy)}
.brand-name{font-family:"Raleway",sans-serif;font-size:25px;font-weight:500;color:var(--navy);letter-spacing:1px}

.nav{position:absolute;right:0;top:0;display:flex;height:114px;font-size:12px;color:#555}
.nav a{display:block;padding:52px 12px 0;color:#555;text-decoration:none}
.nav a.active{background:#f4f4f4;border-top:3px solid var(--blue);padding:49px 13px 0;color:var(--blue);width:61px;margin-right:7px}

.hero{position:absolute;left:0;top:116px;width:919px;height:328px;
  background:linear-gradient(180deg,#3e5a16 0%,#6f8a2c 35%,#a88650 70%,#c8a070 100%);
  box-shadow:0 0 4px rgba(0,0,0,.35)}
.hero-coins{position:absolute;left:0;top:0;width:520px;height:328px;
  background:radial-gradient(ellipse at 50% 55%,#c9c6be 0%,#9c978c 40%,rgba(120,110,80,0) 72%)}
.hero-title{position:absolute;left:489px;top:62px;width:420px;font-family:"Raleway",sans-serif;font-size:28px;font-weight:500;line-height:34px;color:#fff}
.hero-text{position:absolute;left:490px;top:140px;width:410px;font-family:"Raleway",sans-serif;font-size:15px;line-height:21px;color:#fff}
.hero-btn{position:absolute;left:492px;top:230px;width:177px;height:42px;background:var(--blue);color:#fff;
  font-family:"Raleway",sans-serif;font-size:17px;display:flex;align-items:center;justify-content:center}

.features{position:absolute;left:0;top:478px;width:919px;height:199px;background:var(--panel);
  box-shadow:0 0 4px rgba(0,0,0,.3);display:flex}
.feature{border-right:1px solid #ddd;padding:19px 16px 0;position:relative}
.feature:nth-child(1){width:192px}
.feature:nth-child(2){width:199px}
.feature:nth-child(3){width:203px}
.feature:nth-child(4){width:325px;border-right:none;padding:19px 19px 0}
.feature-img{width:161px;height:59px}
.feature h3{font-family:"Raleway",sans-serif;font-weight:400;font-size:18px;color:#222;margin:8px 0 8px}
.feature p{font-size:12px;line-height:17px;color:var(--muted)}
.read-more{display:flex;align-items:center;gap:8px;font-size:11px;color:var(--link);margin-top:6px}
.testimonial-head{display:flex;gap:10px}
.testimonial-head .feature-img{width:121px}
.testimonial-head h3{margin:11px 0 0}
.testimonial-head span{font-size:12px;color:var(--muted);padding-left:3px}
.testimonial p{margin-top:14px;line-height:19px}

.service-col{position:absolute;top:712px;width:310px;height:183px}
.service-col h2{font-family:"Raleway",sans-serif;font-weight:400;font-size:20px;color:#222;margin:8px 0 12px}
.service-col li{list-style:none;font-size:12px;color:#444;line-height:26px;display:flex;gap:9px;align-items:center}
.service-col li.view{font-size:11px;color:var(--link);line-height:16px;padding-left:2px}
.divider{position:absolute;top:712px;width:1px;height:183px;background:linear-gradient(#fff,var(--rule) 30%,var(--rule) 70%,#fff)}

.footer{position:absolute;left:0;top:926px;width:919px;height:234px;background:var(--dark);color:var(--footer-text)}
.footer h4{font-family:"Raleway",sans-serif;font-weight:400;font-size:18px;color:#fff;margin-bottom:22px}
.f-col{position:absolute;top:22px}
.f-col ul{padding-left:15px}
.f-col li{font-size:11.5px;line-height:19px}
.contact-row{display:flex;gap:8px;font-size:11.5px;line-height:19px;align-items:flex-start}
.contact-row svg{margin-top:4px;flex:none}
.map{width:283px;height:117px;border:3px solid #fff;border-radius:2px;
  background:linear-gradient(100deg,#efe6c8 0%,#e8dcb5 45%,#dfe2cf 70%,#9ec4e8 90%)}
.copyright{position:absolute;left:0;top:1160px;width:919px;height:40px;background:var(--darker);color:#ddd;
  font-size:12px;display:flex;align-items:center;justify-content:center}
</style>
</head>
<body>
<div class="page">
  <div class="top-rule"></div>

  <div class="brand">
    <div class="brand-mark"></div>
    <div class="brand-name">TORVEL CAPITAL</div>
  </div>

  <nav class="nav">
    <a class="active" href="#">Home</a>
    <a href="#">About</a>
    <a href="#">Services</a>
    <a href="#">Current Engagements</a>
    <a href="#">Completed Transactions</a>
  </nav>

  <section class="hero">
    <div class="hero-coins" role="img" aria-label="Stack of silver and gold coins on a wooden table"></div>
    <h1 class="hero-title">Torvel Capital, LLC Investment Banking Mergers &amp;Acquisitions</h1>
    <p class="hero-text">Sed ut perspiciatis unde omnis iste natus error sit totam Duis aute irure dolor in reprehenderit in voluptate velit esse cillum rem aperiam eaque ipsa quae ab illo.</p>
    <div class="hero-btn">Read More</div>
  </section>

  <section class="features">
    <div class="feature">
      <div class="feature-img" role="img" aria-label="Hand stacking coins over a financial chart" style="background:linear-gradient(90deg,#9fd0d6,#c7e3df,#d8c98a)"></div>
      <h3>Who we are</h3>
      <p>Lorem ipsum dolor sit amet, consectetur adipisicing elit, sed do eiusmod tempor</p>
      <div class="read-more">Read more <svg width="18" height="6"><path d="M0 3h16M13 0.5l4 2.5-4 2.5" stroke="#2a6fc9" fill="none"/></svg></div>
    </div>
    <div class="feature">
      <div class="feature-img" role="img" aria-label="Hand holding a credit card over a laptop" style="background:linear-gradient(120deg,#2c3240,#5d6a80,#aebbd0)"></div>
      <h3>What we do</h3>
      <p>Lorem ipsum dolor sit amet, consectetur adipisicing elit, sed do eiusmod tempor</p>
      <div class="read-more">Read more <svg width="18" height="6"><path d="M0 3h16M13 0.5l4 2.5-4 2.5" stroke="#2a6fc9" fill="none"/></svg></div>
    </div>
    <div class="feature">
      <div class="feature-img" role="img" aria-label="Globe resting on banknotes" style="background:linear-gradient(90deg,#c9d3e6,#8aa0c8,#3d5f9c)"></div>
      <h3>Our services</h3>
      <p>Lorem ipsum dolor sit amet, consectetur adipisicing elit, sed do eiusmod tempor</p>
      <div class="read-more">Read more <svg width="18" height="6"><path d="M0 3h16M13 0.5l4 2.5-4 2.5" stroke="#2a6fc9" fill="none"/></svg></div>
    </div>
    <div class="feature testimonial">
      <div class="testimonial-head">
        <div class="feature-img" role="img" aria-label="Business team in a bright office meeting room" style="background:linear-gradient(90deg,#5a5a5a,#dcdcdc,#8a98a8)"></div>
        <div><h3>Testimonial</h3><span>Ms Lindqvist</span></div>
      </div>
      <p>Lorem ipsum dolor sit amet, consectetur adipisicing elit, sed do eiusmod tempor incididunt ut labore et dolore magna aliqua.</p>
    </div>
  </section>

  <section class="service-col" style="left:2px">
    <h2>Buy-SideAcquisitions</h2>
    <ul>
      <li><svg width="5" height="8"><path d="M1 1l3 3-3 3" stroke="#2a6fc9" fill="none"/></svg>Lorem ipsum dolor sit amet, consectetur</li>
      <li><svg width="5" height="8"><path d="M1 1l3 3-3 3" stroke="#2a6fc9" fill="none"/></svg>adipisicing elit, sed do eiusmod tempor</li>
      <li><svg width="5" height="8"><path d="M1 1l3 3-3 3" stroke="#2a6fc9" fill="none"/></svg>incididunt ut labore et dolore magna aliqua.</li>
      <li><svg width="5" height="8"><path d="M1 1l3 3-3 3" stroke="#2a6fc9" fill="none"/></svg>Ut enim ad minim veniam</li>
      <li class="view"><svg width="5" height="8"><path d="M1 1l3 3-3 3" stroke="#2a6fc9" fill="none"/></svg>Veiw all</li>
    </ul>
  </section>
  <div class="divider" style="left:294px"></div>
  <section class="service-col" style="left:334px">
    <h2>Recapitalizations</h2>
    <ul>
      <li><svg width="5" height="8"><path d="M1 1l3 3-3 3" stroke="#2a6fc9" fill="none"/></svg>Lorem ipsum dolor sit amet, consectetur</li>
      <li><svg width="5" height="8"><path d="M1 1l3 3-3 3" stroke="#2a6fc9" fill="none"/></svg>adipisicing elit, sed do eiusmod tempor</li>
      <li><svg width="5" height="8"><path d="M1 1l3 3-3 3" stroke="#2a6fc9" fill="none"/></svg>incididunt ut labore et dolore magna aliqua.</li>
      <li><svg width="5" height="8"><path d="M1 1l3 3-3 3" stroke="#2a6fc9" fill="none"/></svg>Ut enim ad minim veniam</li>
      <li class="view"><svg width="5" height="8"><path d="M1 1l3 3-3 3" stroke="#2a6fc9" fill="none"/></svg>Veiw all</li>
    </ul>
  </section>
  <div class="divider" style="left:626px"></div>
  <section class="service-col" style="left:665px">
    <h2>Sell-SideTransactions</h2>
    <ul>
      <li><svg width="5" height="8"><path d="M1 1l3 3-3 3" stroke="#2a6fc9" fill="none"/></svg>Lorem ipsum dolor sit amet, consectetur</li>
      <li><svg width="5" height="8"><path d="M1 1l3 3-3 3" stroke="#2a6fc9" fill="none"/></svg>adipisicing elit, sed do eiusmod tempor</li>
      <li><svg width="5" height="8"><path d="M1 1l3 3-3 3" stroke="#2a6fc9" fill="none"/></svg>incididunt ut labore et dolore magna aliqua.</li>
      <li><svg width="5" height="8"><path d="M1 1l3 3-3 3" stroke="#2a6fc9" fill="none"/></svg>Ut enim ad minim veniam</li>
      <li class="view"><svg width="5" height="8"><path d="M1 1l3 3-3 3" stroke="#2a6fc9" fill="none"/></svg>Veiw all</li>
    </ul>
  </section>

  <footer class="footer">
    <div class="f-col" style="left:15px">
      <h4>Site Linke</h4>
      <ul><li>Home</li><li>About</li><li>Services</li><li>Current Engagements</li><li>Completed Transactions</li></ul>
    </div>
    <div class="f-col" style="left:214px">
      <h4>Resources</h4>
      <ul style="margin-top:2px"><li>Blog</li><li>Articles</li><li>Webinars</li><li>Events</li><li>Downloads</li></ul>
    </div>
    <div class="f-col" style="left:364px">
      <h4>Contact us</h4>
      <div class="contact-row"><svg width="11" height="10"><path d="M0.5 5L5.5 0.5 10.5 5M2 4v5.5h7V4" fill="#ccc"/></svg><span>Request A Free Demo<br>Contact</span></div>
      <div class="contact-row"><svg width="11" height="10"><rect x="3" y="0" width="5" height="10" rx="1" fill="none" stroke="#ccc"/></svg><span>Phone: 555-014-2290</span></div>
      <div class="contact-row"><svg width="11" height="10"><rect x="0.5" y="2" width="10" height="7.5" fill="none" stroke="#ccc"/><rect x="2" y="4" width="2" height="4" fill="#ccc"/></svg><span>Fax: 555-014-2291</span></div>
    </div>
    <div class="f-col" style="left:562px">
      <h4>Our Location</h4>
      <div class="map" role="img" aria-label="Regional road map with office locations marked"></div>
    </div>
  </footer>
  <div class="copyright">© Copyright 2014. All rights reseverd.</div>
</div>
</body>
</html>
```